Larkhollow needs a Webpage Design

We need a webpage for Dr. XYZ who is doing consultancy practice in the area of speech, language, and reading disabilities. He is doing his consultancy practice as "Larkhollow Consultants". Our target market is clients with annual income of $100,000 or more in Chicago area. Our business philosophy is: "...We provide the best evidence-based services/interventions, at an affordable fee, and deal only with clients who seek such services...."

Dr. XYZ's area of research interests are: a) using assistive technology for communication for children with autism, b) early intervention with focus on parent participation, and c) language learning for children birth-to-five years.

He works at a public university whose school color is 'Orange". Home page should show two logos (university and practice). Each page should stand on its own and reflect the content with minimal scrolling. The colors should be subdued (not bright colors) to attract college educated wealthy individuals who are seeking best evidence-based practice in speech, language, and reading for their children.

We need five pages: Home, Consultation, Research, Professional Development, and Contact (with google map directions). The home page should have space for a picture and links for facebook, twitter, and google plus. Other pages should have space for at least one picture and links to pdf files.

The overall design should show healthcare service, evidence-based early intervention with focus on parent participation, and project that we are leaders in the field.

```html
<!DOCTYPE html>
<html lang="en">
<head>
<meta charset="utf-8">
<title>Larkhollow Consultants</title>
<link rel="stylesheet" href="https://fonts.googleapis.com/css2?family=Nunito+Sans:ital,wght@0,300;0,400;0,600;1,400&display=swap">
<style>
:root{
  --blue:#1b73d9;
  --blue-dark:#1868c7;
  --ink:#333333;
  --muted:#5c5c5c;
  --nav:#383838;
  --nav-line:#4c4c4c;
  --band:#f3f3f3;
  --card-border:#e3e3e3;
  --white:#ffffff;
}
*{margin:0;padding:0;box-sizing:border-box}
html,body{width:842px;height:1200px;overflow:hidden;background:var(--white)}
body{position:relative;font-family:"Nunito Sans",Arial,sans-serif;color:var(--ink)}
.abs{position:absolute}
a{color:var(--blue);text-decoration:none}

/* header */
.brand{left:91px;top:20px;text-align:right;line-height:1}
.brand-name{display:block;font-size:29px;font-weight:600;color:var(--blue);letter-spacing:-.3px}
.brand-sub{display:block;font-size:18px;font-weight:400;color:var(--muted);margin-top:2px}
.phone{left:612px;top:29px}
.call{left:638px;top:28px;font-size:13px;color:var(--ink);line-height:1.1}
.call strong{display:block;font-size:20px;font-weight:400;color:var(--blue);margin-top:3px;letter-spacing:.3px}

/* nav */
.nav{left:91px;top:88px;width:659px;height:36px;background:var(--nav);display:flex}
.nav a{color:var(--white);font-size:11.5px;letter-spacing:.3px;display:flex;align-items:center;justify-content:center;border-right:1px solid var(--nav-line)}
.nav a:last-child{border-right:0}

/* hero */
.hero{left:91px;top:124px;width:659px;height:302px;background:linear-gradient(100deg,#ece9e4 0%,#f1ede6 35%,#d9c9b8 60%,#efe6d8 80%,#cdb89c 100%)}
.hero-shadow{left:110px;top:424px;width:621px;height:16px;border-radius:50%;box-shadow:0 8px 10px -4px rgba(0,0,0,.25)}
.hero-caption{left:91px;top:205px;width:433px;height:86px;background:rgba(255,255,255,.85);padding:3px 19px;font-size:22px;line-height:25px;color:var(--blue)}
.dots{left:393px;top:401px;display:flex;gap:5px}
.dots i{width:10px;height:10px;border-radius:50%;background:#222}

/* welcome */
.section-title{width:842px;text-align:center;font-size:19px;font-weight:400;color:var(--ink)}
.welcome-text{left:91px;top:496px;width:659px;text-align:center;font-size:10px;line-height:16px;color:var(--muted)}
.more{font-size:10px;letter-spacing:.2px}
.bar{height:3px;background:#c9c9c9}

/* services */
.band{left:0;top:598px;width:842px;height:322px;background:var(--band)}
.card{top:660px;width:210px;height:241px;background:var(--white);border:1px solid var(--card-border);text-align:center}
.card-shadow{top:896px;width:190px;height:10px;border-radius:50%;box-shadow:0 6px 6px -3px rgba(0,0,0,.2)}
.card .photo{display:block;margin:12px auto 0;width:187px;height:103px}
.card h3{font-size:13px;font-weight:400;color:var(--blue);margin-top:12px}
.card p{font-size:10px;line-height:16px;color:var(--muted);margin:3px 16px 0}
.card a{display:block;font-size:10px;margin-top:7px}

/* research */
.h2{font-size:18px;font-weight:400;color:var(--ink)}
.research-list{left:267px;top:980px;width:260px;list-style:none;font-size:10px;line-height:13px;color:var(--muted)}
.research-list li{position:relative;padding-left:19px;margin-bottom:9px}
.research-list svg{position:absolute;left:0;top:2px}

/* testimonial */
.quote{left:541px;top:982px;width:209px;height:95px;background:var(--white);box-shadow:1px 1px 4px rgba(0,0,0,.2);padding:10px 12px;font-size:9.5px;font-style:italic;line-height:15.5px;color:var(--muted)}
.quote-mark{left:543px;top:972px;font-size:42px;color:#d0d0d0;font-family:Georgia,serif}

/* footer */
.footer{left:0;top:1123px;width:842px;height:77px;background:var(--blue)}
.foot-links{left:91px;top:1136px;font-size:10px;color:var(--white)}
.foot-links a{color:var(--white)}
.foot-links span{margin:0 6px}
.copy{left:91px;top:1167px;font-size:8.5px;color:var(--white)}
.connect{left:675px;top:1136px;font-size:11px;color:var(--white)}
.social{left:675px;top:1157px;display:flex;gap:5px}
.social i{width:22px;height:22px;border-radius:50%;background:var(--white)}
</style>
</head>
<body>

<header>
  <div class="abs brand"><span class="brand-name">Larkhollow</span><span class="brand-sub">Consultants</span></div>
  <svg class="abs phone" width="18" height="18" viewBox="0 0 18 18" aria-hidden="true">
    <rect width="18" height="18" rx="3" fill="#3a3a3a"/>
    <path d="M6 4.5c-.8.3-1.2 1-1.1 1.9.4 3 3.1 6.2 6.3 7 .9.2 1.6-.2 1.9-1l-1.8-1.4-1.2.8c-1.2-.6-2.3-1.9-2.8-3.2l.9-1.1z" fill="#fff"/>
  </svg>
  <div class="abs call">Call Us:<strong>012 555 0147</strong></div>
</header>

<nav class="abs nav">
  <a href="#" style="width:89px">HOME</a>
  <a href="#" style="width:137px">CONSULTATION</a>
  <a href="#" style="width:109px">RESEARCH</a>
  <a href="#" style="width:216px">PROFESSIONAL DEVELOPMENT</a>
  <a href="#" style="width:108px">CONTACT</a>
</nav>

<div class="abs hero-shadow"></div>
<div class="abs hero" role="img" aria-label="Photo of a speech therapist working with a young girl in a bright playroom"></div>
<div class="abs hero-caption">We are doing consultancy practice in the area of speech, language, and reading disabilities.</div>
<div class="abs dots"><i></i><i></i><i></i><i></i></div>

<h2 class="abs section-title" style="top:460px">Welcome to Our Website</h2>
<p class="abs welcome-text">Lorem ipsum dolor sit amet, consect- etuer adipiscing elit, sed diam nonummy nibh euismod tincidunt ut laoreet dolore magna aliquam erat volutpat. Ut wisi enim ad minim veniam, quis nostrud exerci tation ullam. Consectetuer adipiscing elit, sed diam nonummy nibh euismod tincidunt ut laoreet dolore magna aliquam erat volut- pat. Ut wisi enim ad minim veniam, quis nostrud exerci tation ullam.</p>
<a class="abs more" href="#" style="left:386px;top:561px">READ MORE ››</a>
<div class="abs bar" style="left:365px;top:579px;width:112px"></div>

<div class="abs band"></div>
<h2 class="abs section-title" style="top:617px">What We Do</h2>

<div class="abs card-shadow" style="left:101px"></div>
<div class="abs card" style="left:91px">
  <div class="photo" role="img" aria-label="Photo of a therapist and a young boy at a play table" style="background:linear-gradient(120deg,#dfe6ec,#9fbfd8 50%,#e8e2d6)"></div>
  <h3>SPEECH</h3>
  <p>Lorem ipsum dolor sit amet, consect- etuer adipiscing elit, sed diam nonummy nibh euismod tincidunt ut laoreet dolore magna...</p>
  <a href="#">Learn More ››</a>
</div>

<div class="abs card-shadow" style="left:326px"></div>
<div class="abs card" style="left:316px">
  <div class="photo" role="img" aria-label="Photo of a woman talking with a young boy" style="background:linear-gradient(110deg,#f2f2f2,#d9724a 35%,#ece6e2 60%,#4a3a34)"></div>
  <h3>LANGUAGE</h3>
  <p>Lorem ipsum dolor sit amet, consect- etuer adipiscing elit, sed diam nonummy nibh euismod tincidunt ut laoreet dolore magna...</p>
  <a href="#">Learn More ››</a>
</div>

<div class="abs card-shadow" style="left:550px"></div>
<div class="abs card" style="left:540px">
  <div class="photo" role="img" aria-label="Photo of a father reading a book with his son" style="background:linear-gradient(110deg,#ede9e2,#3e4d68 40%,#e9e3da 70%,#c9a98b)"></div>
  <h3>READING DISABILITIES</h3>
  <p>Lorem ipsum dolor sit amet, consect- etuer adipiscing elit, sed diam nonummy nibh euismod tincidunt ut laoreet dolore magna...</p>
  <a href="#">Learn More ››</a>
</div>

<h2 class="abs h2" style="left:91px;top:940px">We Research On</h2>
<div class="abs" role="img" aria-label="Photo of a fountain pen over a dictionary entry for research" style="left:91px;top:983px;width:154px;height:104px;background:linear-gradient(135deg,#f4f1ea,#d8d2c4 60%,#b89a55);border:1px solid #e0e0e0"></div>
<ul class="abs research-list">
  <li><svg width="9" height="8" viewBox="0 0 9 8" aria-hidden="true"><path d="M1 4.2l2.3 2.3L8 1" stroke="#1b73d9" stroke-width="1.8" fill="none"/></svg>Using assistive technology for communication for children with autism..</li>
  <li><svg width="9" height="8" viewBox="0 0 9 8" aria-hidden="true"><path d="M1 4.2l2.3 2.3L8 1" stroke="#1b73d9" stroke-width="1.8" fill="none"/></svg>Early intervention with focus on parent participation</li>
  <li><svg width="9" height="8" viewBox="0 0 9 8" aria-hidden="true"><path d="M1 4.2l2.3 2.3L8 1" stroke="#1b73d9" stroke-width="1.8" fill="none"/></svg>Language learning for children birth-to-five years</li>
</ul>
<a class="abs more" href="#" style="left:267px;top:1070px">READ MORE ››</a>
<div class="abs bar" style="left:267px;top:1086px;width:113px"></div>

<h2 class="abs h2" style="left:541px;top:940px">Testimonials</h2>
<div class="abs quote">Consectetuer adipiscing elit, sed diam nonummy nibh euismod tincidunt ut laoreet dolore magna aliquam erat volut- pat. Ut wisi enim ad minim veniam, quis nostrud exerci tation ullam.</div>
<div class="abs quote-mark">“</div>
<svg class="abs" style="left:597px;top:1076px" width="20" height="16" viewBox="0 0 20 16" aria-hidden="true"><path d="M0 0h20L2 15z" fill="#fff"/><path d="M20 0L2 15" stroke="#ddd"/></svg>
<a class="abs" href="#" style="left:539px;top:1100px;font-size:9.5px">Name goes here</a>

<footer>
  <div class="abs footer"></div>
  <div class="abs foot-links"><a href="#">Home</a><span>/</span><a href="#">Consultation</a><span>/</span><a href="#">Research</a><span>/</span><a href="#">Professional Development</a><span>/</span><a href="#">Contact</a></div>
  <div class="abs copy">Copyright © 2014. Larkhollow Consultants. All Right Reserved</div>
  <div class="abs connect">Connect Us:</div>
  <div class="abs social" aria-label="Social links"><i></i><i></i><i></i></div>
</footer>

</body>
</html>
```